Financial Advisor Resource Firm needs business card design

Need business card design for company in Omaha NE called Meridale Circle. We provide resources to financial advisors....workshop programs, retirement analysis, and insurance planning. I would like to see designs that use grays, greens, black, and white colors. The final design should communicate 'collaboration' and be simple yet attractive to financial planning clients. I will attached our logo and another picture of a puzzle piece coming together. I would like the incorporate the puzzle picture somehow, maybe on the back somehow, with color or just the gray scale....OR, the picture be the front of the card with 'Meridale' definition on it (see upload) and then company logo, employee name, title, address on the back (see ppt uploaded). The following disclosure needs to be included somewhere- Advisory services offered through Stonebrook Assets, LLC.
Updates

I uploaded a svg and ai file of the logo

Target Market(s)

Financial planning clients and financial advisors....so pretty diverse age range of about 40-70.

Industry/Entity Type

Financial Planning

Contact Information for Business Card

Tobias L. Fenwright, MBA
Founder/President
5287 E. Larkin Road
Suite 230
Omaha, NE 68190
Phone- (402) 555-0147
Cell- (402) 555-0183
Fax- (402) 555-0129
email- tobias@meridaleplan.example
web address- www.meridaleplan.example

Colors
1b1b1b
474747
d3d3d3
ffffff
9bcb3c
abd036

Requirements
Must have
• Must include logo provided, must be 2 sided, and must have disclosure...all of these items listed in project description

```html
<!DOCTYPE html>
<html lang="en">
<head>
<meta charset="utf-8">
<title>Meridale Circle — Business Card</title>
<link href="https://fonts.googleapis.com/css2?family=Work+Sans:wght@400;500&display=swap" rel="stylesheet">
<style>
  :root {
    --backdrop: #141414;
    --card: #1b1b1b;
    --card-edge: #262626;
    --silver: #d3d3d3;
    --deboss: #0d0d0d;
    --muted: #474747;
    --green: #9bcb3c;
    --green-light: #abd036;
  }
  * { margin: 0; padding: 0; box-sizing: border-box; }
  html, body { width: 1200px; height: 900px; overflow: hidden; }
  body {
    background: var(--backdrop);
    font-family: "Work Sans", Arial, sans-serif;
    position: relative;
  }
  .card {
    position: absolute;
    left: 250px;
    width: 700px;
    height: 400px;
    background: var(--card);
    border: 1px solid var(--card-edge);
  }
  .card--front { top: 30px; }
  .card--back { top: 470px; }

  .brand {
    position: absolute;
    left: 0; right: 0; top: 168px;
    display: flex;
    align-items: center;
    justify-content: center;
    gap: 16px;
  }
  .brand__dot {
    width: 30px; height: 30px;
    border-radius: 50%;
    border: 3px solid var(--green);
  }
  .brand__name {
    color: var(--silver);
    font-size: 50px;
    font-weight: 500;
    letter-spacing: 2px;
    text-transform: uppercase;
  }

  .identity {
    position: absolute;
    right: 392px;
    top: 118px;
    text-align: right;
    color: var(--deboss);
    font-family: Arial, Helvetica, sans-serif;
  }
  .identity__name { font-size: 24px; margin-bottom: 2px; }
  .identity__title { font-size: 18px; margin-bottom: 14px; }
  .identity__address { font-size: 18px; line-height: 1.3; }

  .divider {
    position: absolute;
    left: 340px; top: 120px;
    width: 1px; height: 120px;
    background: var(--green);
  }

  .contacts {
    position: absolute;
    left: 370px; top: 118px;
    list-style: none;
    color: var(--silver);
    font-size: 18px;
    letter-spacing: 0.5px;
  }
  .contacts li {
    display: flex;
    align-items: center;
    gap: 12px;
    height: 25px;
  }
  .contacts svg { width: 13px; height: 13px; flex: none; }
  .contacts .icon { stroke: var(--green-light); fill: none; stroke-width: 1.4; }

  .disclosure {
    position: absolute;
    left: 0; right: 0; bottom: 26px;
    text-align: center;
    font-size: 11px;
    letter-spacing: 0.4px;
    color: var(--muted);
  }
</style>
</head>
<body>
  <section class="card card--front" aria-label="Card front">
    <div class="brand">
      <span class="brand__dot"></span>
      <span class="brand__name">Meridale Circle</span>
    </div>
  </section>

  <section class="card card--back" aria-label="Card back">
    <div class="identity">
      <p class="identity__name">Tobias L. Fenwright, MBA</p>
      <p class="identity__title">Founder/President</p>
      <p class="identity__address">5287 E. Larkin Road<br>Suite 230 Omaha, NE 68190</p>
    </div>

    <div class="divider"></div>

    <ul class="contacts">
      <li>
        <svg viewBox="0 0 14 14"><path class="icon" d="M3 1.5l2 2.5-1 1.5c.8 1.8 2 3 3.8 3.8l1.5-1 2.5 2-1 2C6 12.5 1.5 8 1 3.3z"/></svg>
        (402) 555-0147
      </li>
      <li>
        <svg viewBox="0 0 14 14"><rect class="icon" x="3.5" y="1" width="7" height="12" rx="1.2"/><line class="icon" x1="6" y1="11" x2="8" y2="11"/></svg>
        (402) 555-0183
      </li>
      <li>
        <svg viewBox="0 0 14 14"><rect class="icon" x="1.5" y="5" width="11" height="6"/><rect class="icon" x="4" y="1.5" width="6" height="3.5"/><rect class="icon" x="4" y="9" width="6" height="3.5"/></svg>
        (402) 555-0129
      </li>
      <li>
        <svg viewBox="0 0 14 14"><rect class="icon" x="1" y="3" width="12" height="8"/><path class="icon" d="M1 3l6 4.5L13 3"/></svg>
        tobias@meridaleplan.example
      </li>
      <li>
        <svg viewBox="0 0 14 14"><circle class="icon" cx="7" cy="7" r="5.8"/><ellipse class="icon" cx="7" cy="7" rx="2.5" ry="5.8"/><line class="icon" x1="1.2" y1="7" x2="12.8" y2="7"/></svg>
        www.meridaleplan.example
      </li>
    </ul>

    <p class="disclosure">Advisory services offered through Stonebrook Assets, LLC.</p>
  </section>
</body>
</html>
```